Eye Catching Email Marketing design

Our health care consulting firm is based in New York City. We sell health care consulting Services to medical practices (doctors). We need a powerful email marketing design to use as one of our primary selling tools to attract new clients. The Design should convey health care knowledge, expertise professionalism, cutting edge technology and the services we offer. <br/>The design should incorporate our logo and its colors (blue and white) but we want it to be eye catching and vibrant, so other colors be included. We are open to the designer's creativity. Any pictures used should show diversity (races)and should include women. Designers can find our logo and other graphics on our website at www harbor ridge advisory.com. Please feel free to ask questions.<br/><br/>

Target Market(s)

Health care professionals, executives and Doctors.

Colors

Designer to choose colors to be used in the design.

Requirements
Nice to have
• What ever the design feels will help make this design vibrant

```html
<!DOCTYPE html>
<html lang="en">
<head>
<meta charset="utf-8">
<title>Harbor Ridge Advisory – Email</title>
<link rel="stylesheet" href="https://fonts.googleapis.com/css2?family=Montserrat:wght@400;500;600;700&display=swap">
<style>
:root{
  --blue:#0b67a8;
  --navy:#0a57a3;
  --sky:#2fa3d6;
  --green:#8cd63a;
  --green-text:#86c73a;
  --white:#ffffff;
  --ink-blue:#2a6fb0;
  --photo-grey:#c9ccd0;
}
*{box-sizing:border-box;margin:0;padding:0}
html,body{width:1200px;height:2563px;overflow:hidden;background:#fff;font-family:"Montserrat",sans-serif}
.email{position:absolute;left:352px;top:0;width:502px;height:2563px;overflow:hidden}
.abs{position:absolute}
.band{position:absolute;left:0;width:502px}
.photo{position:absolute}
.btn{position:absolute;display:flex;align-items:center;justify-content:center;font-size:11px;font-weight:500;background:var(--white);color:var(--ink-blue);height:34px;width:92px}
.btn--green{background:var(--green);color:var(--white)}
.btn--greentext{color:var(--green-text)}
.topbar{top:0;height:26px;background:var(--blue);color:#fff;font-size:9px;display:flex;justify-content:space-around;align-items:center}
.center{text-align:center;left:0;width:502px}
.white{color:#fff}
h1,h2,h3{font-weight:500}
.para{font-size:11px;line-height:16.5px}
.list{font-size:11px;line-height:22px;color:#fff}
.service{position:absolute;top:1425px;width:110px;text-align:center;color:#fff;font-size:10px;font-weight:700;line-height:13px;letter-spacing:-.3px}
.service svg{display:block;margin:0 auto 28px}
.card-text{position:absolute;top:1738px;width:151px;text-align:center;font-size:10.5px;line-height:13px;color:#fff}
.social{position:absolute;top:2451px;width:24px;height:24px;border:1.5px solid #fff;border-radius:50%}
</style>
</head>
<body>
<div class="email">

  <div class="band topbar">
    <span>Your Address</span><span>info@example.com</span><span>www.example.com</span><span>+1 234 56789</span>
  </div>

  <!-- hero -->
  <div class="photo" style="left:0;top:26px;width:502px;height:250px;background:linear-gradient(120deg,#d7d9dc,#eef0f2 55%,#c9cbd0)" role="img" aria-label="Diverse team of doctors meeting around a table in a bright office"></div>
  <div class="abs" style="left:345px;top:90px;width:143px;height:128px;background:rgba(255,255,255,.85)"></div>
  <div class="abs" style="left:351px;top:36px;width:135px;height:50px;background:#fff;display:flex;align-items:center;justify-content:center;text-align:center;font-size:11px;font-weight:600;color:var(--blue);line-height:13px">Harbor Ridge<br>Advisory LLC</div>
  <h1 class="abs" style="left:345px;top:114px;width:143px;text-align:center;font-size:19px;line-height:23px;color:var(--blue);font-weight:500">ADVANCING HEALTHCARE OPERATIONS</h1>
  <svg class="abs" style="left:0;top:230px" width="502" height="50" viewBox="0 0 502 50"><path d="M0 40 Q251 -20 502 40 L502 50 L0 50Z" fill="#fff"/><path d="M0 44 Q251 -12 502 44 L502 50 L0 50Z" fill="var(--green)"/></svg>
  <div class="band" style="top:278px;height:160px;background:var(--green)"></div>
  <h2 class="abs center white" style="top:284px;font-size:19px;font-weight:400">How Can We Help You?</h2>
  <div class="abs" style="left:131px;top:319px;width:268px;height:1px;background:#fff"></div>
  <p class="abs center white para" style="top:332px;padding:0 40px">Lorem ipsum dolor sit amet, consectetur adipiscing elit, sed do eiusmod tempor incididunt ut labore et dolore magna aliqua.</p>
  <div class="btn" style="left:205px;top:380px">Read More</div>

  <!-- welcome -->
  <div class="photo" style="left:0;top:438px;width:251px;height:307px;background:linear-gradient(160deg,#e7e8ea,#cfd3d6)" role="img" aria-label="Smiling doctor holding a tablet with two colleagues behind her"></div>
  <h2 class="abs" style="left:259px;top:488px;font-size:25px;color:var(--sky);font-weight:400">Welcome</h2>
  <h2 class="abs" style="left:259px;top:525px;font-size:23px;line-height:26px;color:var(--green-text);width:230px">Harbor Ridge Advisory</h2>
  <p class="abs para" style="left:259px;top:587px;width:235px;color:var(--ink-blue)">Lorem ipsum dolor sit amet, consectetur adipiscing elit, sed do eiusmod tempor incididunt ut labore et dolore magna.</p>
  <div class="btn btn--green" style="left:259px;top:651px;height:32px">Read More</div>

  <!-- blue feature -->
  <div class="band" style="top:745px;height:260px;background:var(--blue)"></div>
  <h2 class="abs white" style="left:13px;top:793px;font-size:20px;font-weight:600">Lorem Ipsum</h2>
  <p class="abs white para" style="left:15px;top:834px;width:225px">Lorem ipsum dolor sit amet, consectetur adipiscing elit, sed do eiusmod tempor incididunt ut labore et dolore magna.</p>
  <div class="btn btn--greentext" style="left:8px;top:915px">Read More</div>
  <div class="photo" style="left:259px;top:752px;width:236px;height:245px;background:linear-gradient(100deg,#dfe8ea,#b9c9cc 60%,#eef3f3)" role="img" aria-label="Long bright hospital corridor with staff walking"></div>

  <!-- sky feature -->
  <div class="band" style="top:1005px;height:300px;background:var(--sky)"></div>
  <div class="photo" style="left:8px;top:1012px;width:235px;height:243px;background:linear-gradient(170deg,#f3f4f7,#b9c6e6)" role="img" aria-label="Smiling nurse in scrub cap and protective glasses"></div>
  <h2 class="abs white" style="left:251px;top:1042px;width:251px;text-align:center;font-size:20px;font-weight:600">Lorem Ipsum</h2>
  <div class="abs list" style="left:295px;top:1082px">
    <div>✓ Lorem ipsum dolor sit amet</div><div>✓ Lorem ipsum dolor sit amet</div><div>✓ Lorem ipsum dolor sit amet</div><div>✓ Lorem ipsum dolor sit amet</div>
  </div>
  <div class="btn" style="left:402px;top:1186px">Read More</div>

  <!-- services -->
  <svg class="abs" style="left:0;top:1260px" width="502" height="50" viewBox="0 0 502 50"><path d="M0 34 Q251 -20 502 34 L502 50 L0 50Z" fill="#fff"/><path d="M0 40 Q251 -12 502 40 L502 50 L0 50Z" fill="var(--navy)"/></svg>
  <div class="band" style="top:1305px;height:260px;background:var(--navy)"></div>
  <h2 class="abs center white" style="top:1320px;font-size:20px;font-weight:600">Lorem Ipsum</h2>
  <p class="abs center white para" style="top:1360px;padding:0 28px">Lorem ipsum dolor sit amet, consectetur adipiscing elit, sed do eiusmod tempor incididunt ut labore et dolore magna.</p>
  <div class="abs" style="left:117px;top:1407px;width:268px;height:1px;background:rgba(255,255,255,.6)"></div>
  <div class="service" style="left:7px"><svg width="40" height="40" viewBox="0 0 40 40"><path d="M32 12 A14 14 0 1 0 34 22" fill="none" stroke="#fff" stroke-width="4"/><path d="M27 6 L35 12 L27 16Z" fill="#fff"/></svg>REVENUE CYCLE<br>MANAGEMENT</div>
  <div class="service" style="left:133px"><svg width="40" height="40" viewBox="0 0 40 40"><rect x="9" y="4" width="22" height="32" rx="2" fill="none" stroke="#fff" stroke-width="3"/><path d="M14 20 L19 25 L27 15" fill="none" stroke="#fff" stroke-width="3"/></svg>COMPLIANCE<br>MANAGEMENT</div>
  <div class="service" style="left:258px"><svg width="40" height="40" viewBox="0 0 40 40"><circle cx="20" cy="11" r="6" fill="none" stroke="#fff" stroke-width="3"/><path d="M4 22 L12 32 L18 32 M36 22 L28 32 L22 32" fill="none" stroke="#fff" stroke-width="4"/></svg>HEALTHCARE<br>INNOVATION</div>
  <div class="service" style="left:384px"><svg width="40" height="40" viewBox="0 0 40 40"><circle cx="20" cy="12" r="8" fill="none" stroke="#fff" stroke-width="3"/><path d="M8 30 Q20 20 32 30 L32 34 L8 34Z" fill="#fff"/></svg>PRACTICE<br>MANAGEMENT</div>

  <!-- green cards -->
  <svg class="abs" style="left:0;top:1525px" width="502" height="55" viewBox="0 0 502 55"><path d="M0 38 Q251 -15 502 38 L502 55 L0 55Z" fill="var(--green)"/></svg>
  <div class="band" style="top:1575px;height:252px;background:var(--green)"></div>
  <div class="photo" style="left:8px;top:1593px;width:151px;height:121px;background:linear-gradient(160deg,#eef0f2,#c4c8cc)" role="img" aria-label="Dental instruments on a tray"></div>
  <div class="photo" style="left:176px;top:1593px;width:151px;height:121px;background:linear-gradient(160deg,#4a5a7a,#1f3560)" role="img" aria-label="Surgeons operating under theatre lights"></div>
  <div class="photo" style="left:343px;top:1593px;width:151px;height:121px;background:linear-gradient(160deg,#dfe6ee,#3a6fa8)" role="img" aria-label="Medical team reviewing an x-ray"></div>
  <p class="card-text" style="left:8px">I'm a new Text block ready for your content.</p>
  <p class="card-text" style="left:176px">I'm a new Text block ready for your content.</p>
  <p class="card-text" style="left:343px">I'm a new Text block ready for your content.</p>
  <div class="btn" style="left:37px;top:1780px">Read More</div>
  <div class="btn" style="left:205px;top:1780px">Read More</div>
  <div class="btn" style="left:373px;top:1780px">Read More</div>

  <!-- lab -->
  <h2 class="abs" style="left:8px;top:1880px;font-size:19px;color:var(--green-text)">Lorem Ipsum</h2>
  <p class="abs para" style="left:15px;top:1948px;width:220px;color:var(--ink-blue)">Lorem ipsum dolor sit amet, consectetur adipiscing elit, sed do eiusmod tempor incididunt ut labore dolore magna lorem.</p>
  <div class="photo" style="left:251px;top:1827px;width:251px;height:288px;background:linear-gradient(150deg,#f4f5f7,#d9dde2 50%,#3aa58c)" role="img" aria-label="Lab technician pipetting samples into test tubes"></div>

  <!-- letter -->
  <div class="photo" style="left:0;top:2115px;width:251px;height:320px;background:linear-gradient(160deg,#eeeae6,#cfc5bb)" role="img" aria-label="Smiling businesswoman in a white blazer"></div>
  <h2 class="abs" style="left:275px;top:2145px;font-size:19px;color:var(--green-text)">Lorem ipsum</h2>
  <p class="abs" style="left:275px;top:2179px;width:210px;font-size:11px;line-height:19.5px;color:var(--ink-blue)">Lorem ipsum dolor sit amet, consectetur adipiscing elit, sed do eiusmod tempor incididunt ut labore et dolore magna. Sed ut perspiciatis unde omnis iste.</p>
  <p class="abs" style="left:275px;top:2297px;font-size:11px;color:var(--ink-blue)">Kind Regards,</p>
  <div class="abs" style="left:275px;top:2320px;width:150px;height:64px;background:#f1f3f6" role="img" aria-label="Handwritten signature of Daniel Hart"></div>
  <p class="abs" style="left:275px;top:2391px;font-size:11px;font-weight:500;color:var(--green-text)">CEO, COMPANY NAME</p>

  <!-- footer -->
  <svg class="abs" style="left:0;top:2435px" width="502" height="128" viewBox="0 0 502 128"><path d="M0 0 H502 V110 Q251 160 0 110Z" fill="var(--navy)"/></svg>
  <div class="social" style="left:178px"></div>
  <div class="social" style="left:219px"></div>
  <div class="social" style="left:260px"></div>
  <div class="social" style="left:301px"></div>
  <p class="abs center white" style="top:2498px;font-size:9px">Unsubscribe &nbsp;|&nbsp; View Online</p>

</div>
</body>
</html>
```